Every Shelf Set Neatly or ESN Organized needs a business card design. ESN Organized is a professi

We need a business card design that is clean, sharp and conveys a sense of organization. I already have a logo.

Target Market(s)

Families (specifically mothers), small business owners, parents, seniors

Industry/Entity Type

Business

Contact Information for Business Card

My website is www.esnorganized-example.com and my Facebook page is http://www.sociallink-example.com/everyshelfsetneatly. The phone number is 418-552-7094 and I want to be listed as Lorna M. Pelham, Owner

Requirements
Must have
• My logo.

```html
<!DOCTYPE html>
<html lang="en">
<head>
<meta charset="utf-8">
<title>ESN Organized – Business Card</title>
<link rel="stylesheet" href="https://fonts.googleapis.com/css2?family=Montserrat:wght@300;400&family=Open+Sans:ital,wght@0,400;0,700;1,700&display=swap">
<style>
  :root {
    --stage: #141414;
    --paper: #ffffff;
    --brand-blue: #0a79d8;
    --ink-grey: #3a3a3a;
    --on-blue: #ffffff;
  }
  * { margin: 0; padding: 0; box-sizing: border-box; }
  html, body { width: 1200px; height: 900px; overflow: hidden; }
  body {
    background: var(--stage);
    position: relative;
    font-family: "Open Sans", sans-serif;
  }
  .card {
    position: absolute;
    top: 170px;
    width: 347px;
    height: 561px;
    overflow: hidden;
  }
  .card--front { left: 259px; background: var(--paper); }
  .card--back { left: 631px; background: var(--brand-blue); }

  .brand-mark {
    position: absolute;
    top: 204px;
    left: 0;
    width: 100%;
    text-align: center;
    font-family: "Montserrat", sans-serif;
    font-weight: 300;
    font-size: 132px;
    line-height: 1;
    color: var(--brand-blue);
    letter-spacing: -2px;
  }
  .card--front .brand-mark { top: 40px; }

  .owner {
    position: absolute;
    top: 322px;
    width: 100%;
    text-align: center;
  }
  .owner__name {
    font-weight: 700;
    font-size: 22px;
    color: var(--brand-blue);
    letter-spacing: -0.3px;
    line-height: 30px;
  }
  .owner__role {
    font-size: 14px;
    color: var(--ink-grey);
    line-height: 22px;
  }

  .contact {
    position: absolute;
    top: 418px;
    width: 100%;
    list-style: none;
    text-align: center;
    font-size: 14.5px;
    color: var(--ink-grey);
    line-height: 21.5px;
  }
  .contact__icon {
    width: 13px;
    height: 13px;
    vertical-align: -1px;
    margin-right: 5px;
    fill: var(--brand-blue);
  }

  .back-copy {
    position: absolute;
    left: 50%;
    top: 50%;
    width: 561px;
    height: 347px;
    margin-left: -280.5px;
    margin-top: -173.5px;
    transform: rotate(-90deg);
    color: var(--on-blue);
    text-align: center;
  }
  .tagline__lead {
    position: absolute;
    top: 118px;
    width: 100%;
    font-family: "Montserrat", sans-serif;
    font-weight: 300;
    font-size: 26px;
    letter-spacing: 7px;
  }
  .tagline__main {
    position: absolute;
    top: 152px;
    width: 100%;
    font-family: "Montserrat", sans-serif;
    font-weight: 300;
    font-size: 50px;
    letter-spacing: 17px;
    text-indent: 17px;
  }
  .social-link {
    position: absolute;
    top: 284px;
    width: 100%;
    font-style: italic;
    font-weight: 700;
    font-size: 13px;
  }
</style>
</head>
<body>

<section class="card card--front" aria-label="Card front">
  <div class="brand-mark">ESN</div>

  <div class="owner">
    <p class="owner__name">LORNA M. PELHAM</p>
    <p class="owner__role">Owner</p>
  </div>

  <ul class="contact">
    <li>
      <svg class="contact__icon" viewBox="0 0 16 16" aria-hidden="true"><path d="M2 5c0-2 2-3 6-3s6 1 6 3v1h-3V4.5H5V6H2zM4 7h8l2 6H2z"/><circle cx="8" cy="10" r="1.6" fill="#fff"/></svg>418-552-7094
    </li>
    <li>
      <svg class="contact__icon" viewBox="0 0 16 16" aria-hidden="true"><path d="M1 3h14v10H1z"/><path d="M1.5 3.5 8 9l6.5-5.5" fill="none" stroke="#fff" stroke-width="1.3"/></svg>info@esnorganized-example.com
    </li>
    <li>
      <svg class="contact__icon" viewBox="0 0 16 16" aria-hidden="true"><g fill="none" stroke="#0a79d8" stroke-width="2" stroke-linecap="round"><path d="M7 9.5 9.5 7"/><path d="M6 7.5 3.8 9.7a2.3 2.3 0 0 0 3.3 3.3L9 11"/><path d="M10 8.5l2.2-2.2a2.3 2.3 0 0 0-3.3-3.3L7 5"/></g></svg>www.esnorganized-example.com
    </li>
  </ul>
</section>

<section class="card card--back" aria-label="Card back">
  <div class="back-copy">
    <p class="tagline__lead">Every Shelf Set</p>
    <p class="tagline__main">NEATLY</p>
    <p class="social-link">www.sociallink-example.com/everyshelfsetneatly</p>
  </div>
</section>

</body>
</html>
```